One of a kind, 100% Pure & Natural Skincare line needs stunning product label

We need product label design for new natural skincare company called Tolven & Mira Skincare. We create luxurious, 100% pure & natural skincare that is free from ingredients that may be potentially irritating to the skin. No toxins, preservatives or additives. Our initial product is Harbor Face Balm, a nourishing face cream that suits discerning women with mature skin and those with dry/sensitive skin needing extra hydration. Also those that choose to minimize their exposure to environmental toxins. Our brand is simple yet elegant, supporting a holistic, authentic lifestyle and embracing natural skincare.

Target Market(s)

Discerning women with mature skin and those with dry/sensitive skin needing extra hydration. Also those that choose to minimize their exposure to environmental toxins.

Industry/Entity Type

Skin Care Product

Font styles to use
Sans Serif
Script

Colors
f9d9e8
fef1ee

Requirements
Must have
• The Logo.
HARBOR FACE BALM
EMBRACING NATURAL SKINCARE
Labels must be feminine, simple/minimal yet stylish. Uncluttered yet elegant.
This is a very natural product with minimal ingredients.
Nice to have
• The logo can be incorporated in to the label, or It can be left separate as a sticker on top of the jar. The product is a firm balm consistency and is in frosted glass jars with matt silver lids.
Jar height is 45mm, width is 60mm.
Label height: 28mm and length 185mm
Should not have
• Natural or farmers market type theme. No Bold/loud lettering.

```html
<!DOCTYPE html>
<html lang="en">
<head>
<meta charset="utf-8">
<title>Harbor Face Balm – Jar Label</title>
<link rel="stylesheet" href="https://fonts.googleapis.com/css2?family=Montserrat:wght@400;600&family=Bebas+Neue&display=swap">
<style>
  :root {
    --canvas: #ffffff;
    --label-bg: #fcebeb;
    --blush: #f4a5ae;
    --blush-soft: #f8c3c9;
    --ink: #1d1b1b;
    --paper: #ffffff;
  }
  * { box-sizing: border-box; margin: 0; padding: 0; }
  html, body {
    width: 1200px; height: 1200px; overflow: hidden;
    background: var(--canvas);
    font-family: "Montserrat", sans-serif;
    color: var(--ink);
  }
  .canvas {
    position: relative; width: 1200px; height: 1200px;
    display: flex; align-items: center; justify-content: center;
  }
  .label {
    position: relative; width: 1140px; height: 174px;
    background: var(--label-bg);
    box-shadow: 0 2px 10px rgba(0,0,0,0.08);
    overflow: hidden;
  }
  .label__base-band {
    position: absolute; left: 0; right: 0; bottom: 6px; height: 6px;
    background: var(--blush);
  }
  .info-copy {
    position: absolute; left: 15px; top: 20px; width: 250px;
    font-size: 10.5px; line-height: 13px;
  }
  .info-copy p + p { margin-top: 12px; }
  .info-copy strong { font-weight: 600; }

  .brand-art {
    position: absolute; left: 440px; top: 14px; width: 198px; height: 148px;
    border-radius: 6px;
    background: radial-gradient(ellipse 75% 70% at 50% 40%, var(--blush-soft) 0%, rgba(248,195,201,0.55) 60%, rgba(252,235,235,0) 100%);
  }
  .brand-name {
    position: absolute; left: 306px; top: 70px; width: 220px; z-index: 1;
    font-weight: 400; color: var(--ink);
    font-size: 27px; line-height: 30px; letter-spacing: 0.5px;
  }
  .brand-name span { display: block; font-size: 12px; letter-spacing: 7px; line-height: 16px; margin-top: 2px; }

  .title-block {
    position: absolute; left: 568px; top: 18px; width: 212px;
    text-align: right;
  }
  .title-block__claim { font-size: 10.5px; letter-spacing: 0.3px; line-height: 14px; }
  .rule { height: 2px; background: var(--ink); border-radius: 1px; }
  .title-block__claim + .rule { margin: 9px 0 0 82px; }
  .title-block__name { font-size: 24px; letter-spacing: 1px; margin-top: 6px; line-height: 26px; }
  .title-block__product {
    font-family: "Bebas Neue", sans-serif; font-weight: 400; font-size: 52px; line-height: 46px;
    letter-spacing: 0.5px; margin-top: 2px;
  }
  .title-block__product + .rule { margin: 8px 0 0 24px; }
  .title-block__use { font-size: 10.5px; margin-top: 10px; letter-spacing: 0.2px; }

  .origin-band {
    position: absolute; left: 816px; top: 0; width: 14px; height: 156px;
    background: var(--blush);
    display: flex; align-items: center; justify-content: center;
  }
  .origin-band span {
    transform: rotate(-90deg); white-space: nowrap;
    color: var(--paper); font-size: 10.5px; letter-spacing: 1px;
  }

  .directions {
    position: absolute; left: 864px; top: 16px; width: 230px;
    font-size: 10.5px; line-height: 13px;
  }
  .directions strong { font-weight: 600; display: block; }
  .credentials {
    position: absolute; left: 866px; top: 88px; width: 225px; height: 42px;
    display: flex; align-items: center; gap: 11px;
  }
  .directions-rule { position: absolute; left: 866px; top: 138px; width: 218px; height: 1px; background: var(--ink); }
  .contact { position: absolute; left: 864px; top: 146px; font-size: 10.5px; }

  .batch-box {
    position: absolute; left: 1103px; top: 9px; width: 22px; height: 146px;
    background: var(--paper);
    display: flex; align-items: flex-end; justify-content: center; padding-bottom: 8px;
  }
  .batch-box span { transform: rotate(-90deg); font-size: 10.5px; white-space: nowrap; }
</style>
</head>
<body>
<main class="canvas">
  <section class="label" aria-label="Harbor Face Balm jar label">
    <div class="info-copy">
      <p><strong>INGREDIENTS:</strong> tallow from pasture raised goats, frankincense, sandalwood &amp; myrrh essential oils.</p>
      <p><strong>CAUTION:</strong> Keep out of reach of children. If pregnant or breastfeeding, consult your healthcare practitioner. Avoid contact with eyes &amp; sensitive areas.<br>Allergy patch test recommended. If irritation occurs, discontinue use.</p>
    </div>

    <div class="brand-art" role="img" aria-label="Soft pink illustration of a spreading tree behind the brand name"></div>
    <div class="brand-name">Tolven &amp; Mira<span>SKINCARE</span></div>

    <div class="title-block">
      <p class="title-block__claim">100% PURE &amp; NATURAL</p>
      <div class="rule"></div>
      <p class="title-block__name">HARBOR</p>
      <h1 class="title-block__product">FACE BALM</h1>
      <div class="rule"></div>
      <p class="title-block__use">FOR DRY &amp; SENSITIVE SKIN · 50ml</p>
    </div>

    <div class="origin-band"><span>MADE IN AUSTRALIA</span></div>

    <div class="directions">
      <strong>DIRECTIONS:</strong>
      Soften small amount in palm of hand &amp; gently massage into skin as often as required.<br>Store below 25°C
    </div>

    <div class="credentials">
      <svg width="36" height="36" viewBox="0 0 36 36" aria-hidden="true"><circle cx="18" cy="18" r="16" fill="none" stroke="var(--ink)" stroke-width="2"/></svg>
      <svg width="36" height="36" viewBox="0 0 36 36" aria-hidden="true"><circle cx="18" cy="18" r="14" fill="none" stroke="var(--ink)" stroke-width="2"/></svg>
      <svg width="36" height="36" viewBox="0 0 36 36" aria-hidden="true"><circle cx="18" cy="18" r="14" fill="none" stroke="var(--ink)" stroke-width="2"/></svg>
      <svg width="36" height="34" viewBox="0 0 36 34" aria-hidden="true"><polygon points="18,2 34,32 2,32" fill="var(--ink)"/></svg>
      <svg width="40" height="40" viewBox="0 0 40 40" aria-label="Use within 6 months of opening" role="img">
        <path d="M6 20 H34 V34 Q34 37 31 37 H9 Q6 37 6 34 Z" fill="none" stroke="var(--ink)" stroke-width="1.8"/>
        <path d="M4 16 L30 3 L33 8 L7 21 Z" fill="none" stroke="var(--ink)" stroke-width="1.8"/>
        <text x="20" y="33" text-anchor="middle" font-family="Montserrat, sans-serif" font-size="10" fill="var(--ink)">6 M</text>
      </svg>
    </div>
    <div class="directions-rule"></div>
    <p class="contact">info@tolvenandmiraskincare.com.au</p>

    <div class="batch-box"><span>BB:</span></div>
    <div class="label__base-band"></div>
  </section>
</main>
</body>
</html>
```